Laser Tattoo Removal Business Cards

We are looking for a professional business card design for a laser tattoo removal business. Ideally looking for a black business card design. The name of the business is Brightline Tattoo Removal. We place our cards at local tattoo shops so we ideally are looking for something trendy/edgy to draw both male and female clientele in.

Target Market(s)

Male/Female ages 18-60

Contact Information for Business Card

black background ideally.. hoping to stay within greys, whites and black

Font styles to use
Serif
Sans Serif

Colors
121212
a9a9a9
5c5c5c
f5f5f5
ffffff
7f7f7f
606060
848484
9d9d9d

Requirements
Must have
• Employee Info:
• Melissa Thornbury
• Chief Executive Offer
• m: 919.537.2846
• w: 919.362.4178
• f: 919.685.3907
• mthornbury@brightlinetattooremoval.example
• Address:
• 4615 Oakmere Pkwy, Suite 210
• Raleigh, NC 27654
• Website:
• www.brightlinetattooremoval.example
Nice to have
• Myabe business name on back or logo on back and employee info on the front

```html
<!DOCTYPE html>
<html lang="en">
<head>
<meta charset="utf-8">
<title>Brightline Tattoo Removal – Business Cards</title>
<link rel="stylesheet" href="https://fonts.googleapis.com/css2?family=Roboto:wght@400;500&family=Roboto+Condensed:wght@400;500;700&display=swap">
<style>
  :root {
    --page: #8a8a8a;
    --ink: #121212;
    --paper: #f5f5f5;
    --white: #ffffff;
    --grey-dark: #5c5c5c;
    --grey-mid: #7f7f7f;
    --grey-soft: #9d9d9d;
    --grey-light: #a9a9a9;
    --rule: #606060;
  }
  * { margin: 0; padding: 0; box-sizing: border-box; }
  html, body { width: 1200px; height: 960px; overflow: hidden; }
  body {
    position: relative;
    background: var(--page);
    font-family: "Roboto", sans-serif;
  }
  .card {
    position: absolute;
    left: 313px;
    width: 600px;
    height: 343px;
  }
  .card--front { top: 113px; background: var(--paper); }
  .card--back { top: 472px; background: var(--ink); }

  .brand {
    position: absolute;
    font-family: "Roboto Condensed", sans-serif;
    font-weight: 500;
    text-transform: uppercase;
    text-align: center;
    line-height: 1.15;
  }
  .card--front .brand {
    left: 35px; top: 58px; width: 210px;
    color: var(--ink);
    font-size: 30px;
    letter-spacing: 2px;
  }
  .card--front .brand small {
    display: block;
    font-size: 17px;
    letter-spacing: 3px;
    margin-top: 14px;
  }
  .card--back .brand {
    left: 0; top: 108px; width: 600px;
    color: var(--grey-light);
    font-size: 46px;
    letter-spacing: 3px;
  }
  .card--back .brand small {
    display: block;
    font-size: 20px;
    letter-spacing: 4px;
    margin-top: 30px;
  }

  .person {
    position: absolute;
    right: 32px; top: 204px;
    text-align: right;
  }
  .person__name {
    font-family: "Roboto Condensed", sans-serif;
    font-weight: 500;
    font-size: 21px;
    color: var(--ink);
    line-height: 24px;
  }
  .person__marker {
    position: absolute;
    left: 576px; top: 208px;
    width: 24px; height: 18px;
    background: var(--ink);
  }
  .rule {
    position: absolute;
    left: 35px; top: 229px;
    width: 533px; height: 2px;
    background: var(--rule);
  }
  .person__title {
    position: absolute;
    right: 32px; top: 234px;
    font-size: 14.5px;
    color: var(--grey-mid);
  }
  .address {
    position: absolute;
    right: 32px; top: 259px;
    text-align: right;
    font-size: 13.5px;
    line-height: 18.5px;
    color: var(--grey-dark);
    font-style: normal;
  }
  .contacts {
    position: absolute;
    left: 33px; top: 240px;
    list-style: none;
    font-size: 13.5px;
    line-height: 19px;
    color: var(--grey-dark);
  }
  .contacts li { display: flex; align-items: center; }
  .contacts svg { width: 14px; height: 13px; margin-right: 8px; fill: var(--ink); flex: none; }

  .back__web {
    position: absolute;
    left: 0; top: 292px; width: 600px;
    text-align: center;
    color: var(--white);
    font-size: 13.5px;
    letter-spacing: 2.6px;
  }
</style>
</head>
<body>

<section class="card card--front" aria-label="Business card front">
  <div class="brand">Brightline<small>Tattoo Removal</small></div>

  <div class="person"><div class="person__name">MELISSA THORNBURY</div></div>
  <div class="person__marker"></div>
  <div class="rule"></div>
  <div class="person__title">Chief Executive Offer</div>

  <ul class="contacts">
    <li>
      <svg viewBox="0 0 14 14"><path d="M3 1l2.5 3-1.5 1.6c.8 1.8 2.2 3.2 4 4L9.6 8 13 10.5 11.5 13C6 12.5 1.5 8 1 2.5z"/></svg>
      919.362.4178
    </li>
    <li>
      <svg viewBox="0 0 14 14"><path d="M4 0h6v14H4zM5 1.5v9.5h4V1.5z"/></svg>
      919.537.2846
    </li>
    <li>
      <svg viewBox="0 0 14 14"><path d="M3 1h8v3H3zM1 5h12v6h-2v2H3v-2H1zM4 9v3h6V9z"/></svg>
      919.685.3907
    </li>
    <li>
      <svg viewBox="0 0 14 14"><path d="M1 3h12v1L7 8 1 4zM1 5.5l6 4 6-4V11H1z"/></svg>
      mthornbury@brightlinetattooremoval.example
    </li>
  </ul>

  <address class="address">
    4615 Oakmere Pkwy, Suite 210<br>
    Raleigh, NC 27654<br>
    www.brightlinetattooremoval.example
  </address>
</section>

<section class="card card--back" aria-label="Business card back">
  <div class="brand">Brightline<small>Tattoo Removal</small></div>
  <div class="back__web">www.brightlinetattooremoval.example</div>
</section>

</body>
</html>
```